Business Card Update, need to bring life to the card, two sided color

We need a new business card design, are moving and changing addresses and need a new look, we have the logos already attached but need a new style moving forward. Can incorporate the color of the logo (The Green) as well, maybe a solid back? We deal with safety products revolving around static electricity and safety lighting. Would like to keep same font in second logo as well.

Target Market(s)

Electrical Safety, Lighting

Contact Information for Business Card

Dale Fenwick
Vice President
Office: 770-555-4821
Cell: 770-555-3067
dale@tkfenwick.example
www.tkfenwick.example
4700 West Harbor Boulevard
Suite #150
Roswell, GA 30076

Font styles to use
Serif
Sans Serif

Requirements
Must have
• Since 1918
Nice to have
• Could use the 100 Year Logo for back of card, would like the back of card to be the same green as logo.
Should not have
• No black cards please.

```html
<!DOCTYPE html>
<html lang="en">
<head>
<meta charset="utf-8">
<title>Business Card – Front and Back</title>
<link rel="stylesheet" href="https://fonts.googleapis.com/css2?family=Open+Sans:ital,wght@0,400;0,600;0,700;0,800;1,400&display=swap">
<style>
  :root {
    --brand-green: #008f55;
    --brand-green-dark: #007a48;
    --paper: #ffffff;
    --paper-shade: #e6e6e6;
    --ink: #1e1e1e;
    --back-text: #e4ece8;
    --stage: #d9dcdb;
  }
  * { box-sizing: border-box; margin: 0; padding: 0; }
  html, body { width: 1200px; height: 900px; overflow: hidden; }
  body {
    background: var(--stage);
    font-family: "Open Sans", Arial, sans-serif;
    display: flex; flex-direction: column; align-items: center; justify-content: center;
    gap: 40px;
  }
  .card {
    width: 660px; height: 377px; border-radius: 18px;
    position: relative; overflow: hidden;
    box-shadow: 0 10px 28px rgba(0,0,0,.22);
  }
  /* Front */
  .card-front {
    background: radial-gradient(ellipse at 62% 70%, var(--paper) 30%, var(--paper-shade) 100%);
    color: var(--ink);
  }
  .top-band {
    position: absolute; left: 0; top: 26px; width: 420px; height: 62px;
    background: var(--brand-green);
  }
  .holder { position: absolute; left: 34px; top: 32px; color: var(--paper); }
  .holder-name { font-weight: 800; font-size: 25px; line-height: 1.1; }
  .holder-title { font-style: italic; font-size: 16px; opacity: .9; }
  .front-brand {
    position: absolute; left: 398px; top: 30px; display: flex; align-items: center; gap: 10px;
  }
  .brand-mark {
    width: 54px; height: 54px; border-radius: 50%;
    background: var(--paper); border: 5px solid var(--brand-green); flex: none;
  }
  .brand-text { display: flex; flex-direction: column; }
  .brand-name { font-weight: 800; font-size: 17px; color: var(--brand-green); line-height: 1.15; width: 200px; }
  .brand-since { font-weight: 600; font-size: 12px; color: var(--ink); letter-spacing: .08em; margin-top: 2px; }
  .contact-list { position: absolute; left: 34px; bottom: 36px; list-style: none; font-size: 14px; line-height: 1.6; }
  .contact-list li { display: flex; align-items: center; gap: 10px; }
  .contact-list svg { width: 14px; height: 14px; fill: var(--brand-green); flex: none; }
  .contact-label { color: var(--brand-green); font-weight: 600; }
  .web-domain { color: var(--brand-green); }
  .address { position: absolute; right: 34px; bottom: 36px; text-align: right; font-size: 14px; line-height: 1.6; }
  .bottom-band {
    position: absolute; right: 0; bottom: 0; width: 560px; height: 12px;
    background: var(--brand-green);
    clip-path: polygon(14px 0, 100% 0, 100% 100%, 0 100%);
  }
  /* Back */
  .card-back {
    background: linear-gradient(135deg, var(--brand-green) 0%, var(--brand-green-dark) 100%);
    display: flex; align-items: center; justify-content: center; gap: 22px;
  }
  .back-mark {
    width: 110px; height: 110px; border-radius: 50%;
    border: 8px solid var(--back-text); flex: none;
  }
  .back-text { display: flex; flex-direction: column; }
  .back-name { font-weight: 800; font-size: 34px; color: var(--back-text); line-height: 1.15; width: 330px; }
  .back-since { font-weight: 600; font-size: 16px; color: var(--back-text); letter-spacing: .12em; margin-top: 8px; }
</style>
</head>
<body>
  <section class="card card-front" aria-label="Business card front">
    <div class="top-band"></div>
    <div class="holder">
      <p class="holder-name">Dale Fenwick</p>
      <p class="holder-title">Vice President</p>
    </div>
    <div class="front-brand">
      <span class="brand-mark"></span>
      <span class="brand-text">
        <span class="brand-name">T.K. Fenwick Manufacturing Co.</span>
        <span class="brand-since">SINCE 1918</span>
      </span>
    </div>
    <ul class="contact-list">
      <li><svg viewBox="0 0 24 24"><path d="M6.6 10.8a15 15 0 0 0 6.6 6.6l2.2-2.2c.3-.3.7-.4 1-.2 1.1.4 2.3.6 3.6.6.6 0 1 .4 1 1V20c0 .6-.4 1-1 1A17 17 0 0 1 3 4c0-.6.4-1 1-1h3.5c.6 0 1 .4 1 1 0 1.3.2 2.5.6 3.6.1.3 0 .7-.2 1z"/></svg><span><span class="contact-label">Office:</span> 770-555-4821</span></li>
      <li><svg viewBox="0 0 24 24"><path d="M7 1h10a2 2 0 0 1 2 2v18a2 2 0 0 1-2 2H7a2 2 0 0 1-2-2V3a2 2 0 0 1 2-2zm0 3v14h10V4z"/></svg><span><span class="contact-label">Cell:</span> 770-555-3067</span></li>
      <li><svg viewBox="0 0 24 24"><path d="M2 5h20v14H2zm2 2v.5l8 5 8-5V7zm0 3v7h16v-7l-8 5z"/></svg>dale@tkfenwick.example</li>
      <li><svg viewBox="0 0 24 24"><circle cx="12" cy="12" r="10"/></svg><span>www.<span class="web-domain">tkfenwick</span>.example</span></li>
    </ul>
    <p class="address">4700 West Harbor Boulevard<br>Suite #150<br>Roswell, GA 30076</p>
    <div class="bottom-band"></div>
  </section>

  <section class="card card-back" aria-label="Business card back">
    <span class="back-mark"></span>
    <span class="back-text">
      <span class="back-name">T.K. Fenwick Manufacturing Co.</span>
      <span class="back-since">SINCE 1918</span>
    </span>
  </section>
</body>
</html>
```